Business card design needed

We require business cards for our young and innovative construction team.

Our business is Quarry Ridge Builders and we have used Lime, Navy and white with our colours so far.

We would like business cards that show our passion for perfection and detail, communication and management.

Looking forward to seeing the deigns!!

Communication

Dan Ferrante
Quarry Ridge Builders Pty Ltd
PO Box 617 Birchgrove NSW 2041
Mobile: 0471 362 907
Email: dferrante@quarryridgebuilders.com.au
Web: www.quarryridgebuilders.com.au

```html
<!DOCTYPE html>
<html lang="en">
<head>
<meta charset="utf-8">
<title>Quarry Ridge Builders — Business Cards</title>
<link rel="stylesheet" href="https://fonts.googleapis.com/css2?family=Oswald:wght@400;500;600&family=Open+Sans:wght@400;600&display=swap">
<style>
  :root {
    --canvas: #e9e6e1;
    --card-black: #141414;
    --card-edge: #262626;
    --lime: #9acd2a;
    --lime-deep: #7fb51c;
    --navy: #5a7dbd;
    --text-light: #d9d9d9;
  }
  * { box-sizing: border-box; margin: 0; padding: 0; }
  html, body {
    width: 1200px; height: 1024px; overflow: hidden;
    background: var(--canvas);
  }
  .sheet {
    position: relative; width: 1200px; height: 1024px;
    display: flex; flex-direction: column; align-items: center; justify-content: center; gap: 60px;
  }
  .card {
    position: relative; width: 640px; height: 390px;
    background: radial-gradient(ellipse at 40% 35%, #222 0%, var(--card-black) 70%);
    border-radius: 4px;
    box-shadow: 0 14px 30px rgba(0,0,0,.28);
    overflow: hidden;
  }

  /* Front */
  .card-front .brand {
    position: absolute; left: 70px; top: 120px;
    display: flex; align-items: center; gap: 18px;
  }
  .brand-square {
    width: 46px; height: 46px; background: var(--lime);
  }
  .brand-name {
    font-family: "Oswald", sans-serif; font-weight: 500;
    font-size: 50px; letter-spacing: 1px; color: var(--navy); line-height: 1;
  }
  .card-front .tagline {
    position: absolute; left: 70px; top: 210px;
    font-family: "Oswald", sans-serif; font-weight: 400;
    font-size: 21px; color: var(--lime); letter-spacing: .3px;
  }

  /* Back */
  .card-back .edge-band {
    position: absolute; left: 0; top: 0; bottom: 0; width: 46px;
    background: linear-gradient(90deg, var(--lime-deep), var(--lime));
  }
  .card-back .holder-name {
    position: absolute; left: 96px; top: 44px;
    font-family: "Oswald", sans-serif; font-weight: 600;
    font-size: 32px; color: var(--lime);
  }
  .contact-list {
    position: absolute; left: 96px; top: 112px; list-style: none;
    font-family: "Open Sans", sans-serif; font-size: 15px; color: var(--text-light);
  }
  .contact-list li { display: flex; align-items: flex-start; gap: 12px; margin-bottom: 12px; line-height: 1.4; }
  .contact-list svg { flex: none; width: 16px; height: 16px; margin-top: 2px; fill: var(--lime); }
  .card-back .brand-small {
    position: absolute; right: 44px; bottom: 44px;
    display: flex; align-items: center; gap: 10px;
  }
  .brand-small .brand-square { width: 24px; height: 24px; }
  .brand-small .brand-name { font-size: 28px; }
</style>
</head>
<body>
<main class="sheet">

  <section class="card card-front" aria-label="Card front">
    <div class="brand">
      <span class="brand-square"></span>
      <span class="brand-name">Quarry Ridge Builders</span>
    </div>
    <p class="tagline">Quarry Ridge Builders is a residential construction company</p>
  </section>

  <section class="card card-back" aria-label="Card back">
    <div class="edge-band"></div>
    <h1 class="holder-name">Dan Ferrante</h1>
    <ul class="contact-list">
      <li>
        <svg viewBox="0 0 16 16" aria-hidden="true"><rect x="4" y="1" width="8" height="14" rx="1.5"/><rect x="5.5" y="3" width="5" height="8" fill="#141414"/></svg>
        <span>0471 362 907</span>
      </li>
      <li>
        <svg viewBox="0 0 16 16" aria-hidden="true"><rect x="1" y="3" width="14" height="10" rx="1"/><path d="M1.5 3.5 8 9l6.5-5.5" stroke="#141414" stroke-width="1.4" fill="none"/></svg>
        <span>dferrante@quarryridgebuilders.com.au</span>
      </li>
      <li>
        <svg viewBox="0 0 16 16" aria-hidden="true"><circle cx="8" cy="8" r="7"/><path d="M1 8h14M8 1c-3 3-3 11 0 14M8 1c3 3 3 11 0 14" stroke="#141414" stroke-width="1.2" fill="none"/></svg>
        <span>www.quarryridgebuilders.com.au</span>
      </li>
      <li>
        <svg viewBox="0 0 16 16" aria-hidden="true"><path d="M8 1a5 5 0 0 0-5 5c0 4 5 9 5 9s5-5 5-9a5 5 0 0 0-5-5z"/><circle cx="8" cy="6" r="1.8" fill="#141414"/></svg>
        <span>PO Box 617 Birchgrove<br>NSW 2041</span>
      </li>
    </ul>
    <div class="brand brand-small">
      <span class="brand-square"></span>
      <span class="brand-name">Quarry Ridge Builders</span>
    </div>
  </section>

</main>
</body>
</html>
```